Natural Light/Organic/Documentary Photography Business

I like a simple, approachable, feminine, earthy/organic feel. Earth/neutral tones, nothing too loud or obnoxious. I like the watercolor look. I don't want anything too trendy or something I'll get tired of after a couple months. As far as colors, I am much more a fan of cream/taupe/blue/green...not a fan of pink or purple at all.

Target Market(s)

Weddings & Families

Industry/Entity Type

Wedding Photography

Contact Information for Business Card

website, email, phone number

Font styles to use
Other font styles liked:
• Horizontes, Gotham

Colors

Designer to choose colors to be used in the design.

Requirements
Must have
• Website: www.mirelhatchway.com
• Phone: 418.629.5073
• Email: mirel@mirelhatchway.com
Nice to have
• I like the watercolor look but its not necessary. I like simple/earthy tones. Nothing too loud or distracting. Simple & feminine without being too girly. I like an approachable/soft feel.
• Instagram: www.instagram.com/mirelhatchwayphotography/
Should not have
• NO loud colors or design or pattern. I do not want a photo of a camera or lens or anything cheesy like that.

```html
<!DOCTYPE html>
<html lang="en">
<head>
<meta charset="utf-8">
<title>Mirel Hatchway – Business Card</title>
<link rel="stylesheet" href="https://fonts.googleapis.com/css2?family=Open+Sans:wght@400;600&display=swap">
<style>
  :root {
    --backdrop: #ebebeb;
    --card: #ffffff;
    --taupe: #8c7e74;
    --ink: #4a4440;
    --band-text: #ffffff;
  }
  * { box-sizing: border-box; margin: 0; padding: 0; }
  html, body {
    width: 1200px; height: 799px; overflow: hidden;
    background: var(--backdrop);
    font-family: "Open Sans", Arial, sans-serif;
  }
  .canvas { position: relative; width: 1200px; height: 799px; }
  .card {
    position: absolute; left: 313px; width: 584px; height: 334px;
    background: var(--card);
  }
  .card--front { top: 50px; }
  .card--back { top: 412px; }

  .monogram-name {
    position: absolute; left: 30px; top: 96px;
    color: var(--taupe); font-weight: 600; font-size: 40px; line-height: 1.15;
  }
  .edge-tab {
    position: absolute; right: 0; top: 196px; width: 12px; height: 101px;
    background: var(--taupe); border-radius: 8px 0 0 8px;
  }
  .contact-name {
    position: absolute; right: 41px; top: 186px;
    color: var(--taupe); font-weight: 600; font-size: 20px; letter-spacing: 0.2px;
  }
  .contact-list { position: absolute; right: 41px; top: 225px; list-style: none; }
  .contact-item {
    display: flex; justify-content: flex-end; align-items: center;
    height: 19.3px; color: var(--ink); font-size: 14px;
  }
  .contact-icon { width: 13px; height: 13px; margin-left: 10px; flex: none; }
  .contact-icon * { fill: var(--taupe); }

  .wordmark {
    position: absolute; left: 0; right: 0; top: 130px; text-align: center;
    color: var(--taupe); font-weight: 400; font-size: 36px; letter-spacing: 1px;
  }
  .web-band {
    position: absolute; left: 0; right: 0; top: 277px; height: 24px;
    background: var(--taupe); color: var(--band-text);
    font-size: 14px; letter-spacing: 4.4px; text-align: center; line-height: 24px;
    font-weight: 600;
  }
</style>
</head>
<body>
<main class="canvas">
  <section class="card card--front">
    <div class="monogram-name">Mirel<br>Hatchway</div>
    <div class="contact-name">Mirel Hatchway</div>
    <ul class="contact-list">
      <li class="contact-item">418.629.5073
        <svg class="contact-icon" viewBox="0 0 16 16" aria-hidden="true"><path d="M1 6c0-3 3-4 7-4s7 1 7 4v1h-4V5H5v2H1z"/><path d="M4 8l2-2h4l2 2 2 6H2z"/></svg>
      </li>
      <li class="contact-item">mirel@mirelhatchway.com
        <svg class="contact-icon" viewBox="0 0 16 16" aria-hidden="true"><rect x="1" y="3" width="14" height="10" rx="1"/></svg>
      </li>
      <li class="contact-item">www.mirelhatchway.com
        <svg class="contact-icon" viewBox="0 0 16 16" aria-hidden="true"><circle cx="8" cy="8" r="7"/></svg>
      </li>
      <li class="contact-item">mirelhatchwayphotography
        <svg class="contact-icon" viewBox="0 0 16 16" aria-hidden="true"><rect x="1" y="1" width="14" height="14" rx="3"/></svg>
      </li>
    </ul>
    <div class="edge-tab"></div>
  </section>

  <section class="card card--back">
    <div class="wordmark">Mirel Hatchway</div>
    <div class="web-band">WWW.MIRELHATCHWAY.COM</div>
  </section>
</main>
</body>
</html>
```